Health and Wellness company needs flyer to promote free seminar

Corvella Motion studio is a health and wellness company that offers an exercise program designed by physical therapists to help relieve pain and improve mobility. Our business is a new concept that is not well understood by the public. In order to promote our business we offer a free seminar where we present information regarding the underlying cause of pain and tightness. During the seminar we also perform a posture screen and movement testing for all participants.

Target Market(s)

Mostly healthy and active women ages 25-65

Industry/Entity Type

Health And Wellness

Font styles to use
Sans Serif

Colors

Designer to choose colors to be used in the design.

Requirements
Must have
• Title: Eliminate Pain and Tightness For Good
• Paragraph: Corvella Motion Studio offers a free 60 minute seminar: "The Busy Walker's Manual for Stretching and Living Lighter."
• What to Expect:
• • Identify the underlying cause of your pain and mobility issues
• • Expose what gets in the way of you moving and feeling better
• • Learn why traditional exercises don’t help and can actually make the problem worse
• • Reveal what your posture is saying and how that impacts you
• • Experience your muscle imbalances through movement tests
• • Discover the training method that realigns your posture, increases your mobility and reduces your pain
• Call to action: RSVP online at corvellamotionstudio.com
Nice to have
• Use a relevant image showing a female dealing with tightness in the low back, legs, etc.
• Emphasize that the seminar is FREE.
• Make the call to action prominent.

```html
<!DOCTYPE html>
<html lang="en">
<head>
<meta charset="utf-8">
<title>Corvella Motion Studio – Free Seminar</title>
<link href="https://fonts.googleapis.com/css2?family=Nunito:wght@700;800;900&family=Open+Sans:wght@400;600&display=swap" rel="stylesheet">
<style>
  :root{
    --navy:#3b3c69;
    --navy-dark:#35375c;
    --orange:#f7941d;
    --band:#ebebeb;
    --white:#ffffff;
    --ink:#1c1c1c;
    --tick:#e8a431;
  }
  *{margin:0;padding:0;box-sizing:border-box}
  html,body{width:846px;height:1200px;overflow:hidden;background:var(--white)}
  .flyer{position:relative;width:846px;height:1200px;overflow:hidden;background:var(--white);font-family:"Open Sans",sans-serif}

  .brand{position:absolute;top:26px;left:0;width:846px;display:flex;justify-content:center;align-items:center;gap:18px}
  .brand-mark{width:62px;height:62px;border:9px solid var(--orange);border-radius:6px}
  .brand-name{font-family:"Nunito",sans-serif;font-weight:800;font-size:44px;color:var(--navy);letter-spacing:-.5px}

  .title-band{position:absolute;top:142px;left:2px;width:844px;height:82px;background:var(--band);display:flex;align-items:center;justify-content:center}
  .title{font-family:"Nunito",sans-serif;font-weight:900;font-size:45px;color:var(--navy-dark);letter-spacing:-.5px}
  .title .accent{color:var(--orange)}

  .backdrop{position:absolute;inset:0}

  .photo{position:absolute;left:510px;top:236px;width:336px;height:760px;
    border-radius:170px 0 0 0;
    background:linear-gradient(170deg,#8a6650 0%,#b48e7e 24%,#dcc2bc 45%,#e6cfca 70%,#d9bdb6 100%)}

  .burst{position:absolute;left:46px;top:246px;width:236px;height:236px}
  .burst span{position:absolute;left:34px;top:34px;width:168px;height:168px;background:var(--orange)}
  .burst span:nth-child(2){transform:rotate(15deg)}
  .burst span:nth-child(3){transform:rotate(30deg)}
  .burst span:nth-child(4){transform:rotate(45deg)}
  .burst span:nth-child(5){transform:rotate(60deg)}
  .burst span:nth-child(6){transform:rotate(75deg)}
  .burst-text{position:absolute;inset:0;display:flex;flex-direction:column;align-items:center;justify-content:center;
    transform:rotate(-8deg);color:var(--white);font-family:"Nunito",sans-serif;line-height:1}
  .burst-free{font-size:56px;font-weight:900;letter-spacing:2px}
  .burst-length{font-size:28px;font-weight:700;margin-top:2px}
  .burst-seminar{font-size:38px;font-weight:900;letter-spacing:1px;margin-top:2px}

  .expect{position:absolute;left:40px;top:520px;width:460px;color:var(--white)}
  .expect-heading{font-family:"Nunito",sans-serif;font-weight:800;font-size:34px;margin-bottom:22px}
  .expect-list{list-style:none}
  .expect-list li{position:relative;padding-left:32px;font-size:17px;line-height:24px;min-height:69px}
  .expect-list li svg{position:absolute;left:4px;top:6px;width:15px;height:13px}
  .expect-list .verb{text-decoration:underline;text-underline-offset:2px}

  .seminar-name{position:absolute;left:18px;top:1072px;width:500px;text-align:center;color:var(--white);
    font-family:"Nunito",sans-serif;font-weight:800;font-size:29px;line-height:38px}

  .rsvp{position:absolute;left:550px;top:1066px;width:282px;height:80px;border:2px solid var(--white);border-radius:16px}
  .rsvp-label{position:absolute;top:-16px;left:50%;transform:translateX(-50%);background:var(--orange);padding:0 10px;white-space:nowrap;
    font-family:"Nunito",sans-serif;font-weight:900;font-size:23px;color:var(--ink)}
  .rsvp-url{position:absolute;top:27px;left:0;width:100%;text-align:center;font-family:"Nunito",sans-serif;font-weight:700;font-size:19px;color:var(--white)}
</style>
</head>
<body>
<main class="flyer">
  <header class="brand">
    <div class="brand-mark"></div>
    <div class="brand-name">Corvella Motion Studio</div>
  </header>

  <div class="title-band">
    <h1 class="title">Eliminate <span class="accent">Pain &amp; Tightness</span> for Good</h1>
  </div>

  <svg class="backdrop" width="846" height="1200" viewBox="0 0 846 1200" aria-hidden="true">
    <polygon points="0,420 846,364 846,1200 0,1200" fill="var(--navy)"/>
  </svg>

  <div class="photo" role="img" aria-label="Woman seen from behind holding her lower back in discomfort"></div>

  <svg class="backdrop" width="846" height="1200" viewBox="0 0 846 1200" aria-hidden="true">
    <polygon points="0,1050 846,972 846,1200 0,1200" fill="var(--orange)"/>
  </svg>

  <div class="burst">
    <span></span><span></span><span></span><span></span><span></span><span></span>
    <div class="burst-text">
      <div class="burst-free">FREE</div>
      <div class="burst-length">60 minute</div>
      <div class="burst-seminar">SEMINAR</div>
    </div>
  </div>

  <section class="expect">
    <h2 class="expect-heading">What to Expect</h2>
    <ul class="expect-list">
      <li><svg viewBox="0 0 15 13"><path d="M1 7l4 4 9-10" fill="none" stroke="var(--tick)" stroke-width="2"/></svg><span class="verb">IDENTIFY</span> the underlying cause of<br>your pain and mobility issues.</li>
      <li><svg viewBox="0 0 15 13"><path d="M1 7l4 4 9-10" fill="none" stroke="var(--tick)" stroke-width="2"/></svg><span class="verb">EXPOSE</span> what gets in the way of<br>you moving and feeling better.</li>
      <li><svg viewBox="0 0 15 13"><path d="M1 7l4 4 9-10" fill="none" stroke="var(--tick)" stroke-width="2"/></svg><span class="verb">LEARN</span> why traditional exercises don’t help and can<br>actually make the problem worse.</li>
      <li><svg viewBox="0 0 15 13"><path d="M1 7l4 4 9-10" fill="none" stroke="var(--tick)" stroke-width="2"/></svg><span class="verb">REVEAL</span> what your posture is saying and how that<br>impacts you.</li>
      <li><svg viewBox="0 0 15 13"><path d="M1 7l4 4 9-10" fill="none" stroke="var(--tick)" stroke-width="2"/></svg><span class="verb">EXPERIENCE</span> your muscle imbalances through<br>movement tests.</li>
      <li><svg viewBox="0 0 15 13"><path d="M1 7l4 4 9-10" fill="none" stroke="var(--tick)" stroke-width="2"/></svg><span class="verb">DISCOVER</span> the training method that realigns your<br>posture, increases your mobility and reduces your<br>pain.</li>
    </ul>
  </section>

  <p class="seminar-name">“The Busy Walker's Manual for Stretching and Living Lighter”</p>

  <div class="rsvp">
    <div class="rsvp-label">RSVP online at</div>
    <div class="rsvp-url">corvellamotionstudio.com</div>
  </div>
</main>
</body>
</html>
```